Website for software company "velora"

We need a website for our software company/startup named "velora". We are developing several products (currently 3 standard-software products) which are all in different sectors, but all our products are available for Laptops/PC/Mobile Phones/Tablets, ... We do also create custom software and support our customers with consulting to optimize their processes.
We already have a Logo which you can find in the attached files.
We are a young team of 4 members (two founders and 2 employees).

To get an idea of our products -> the first one is a planning software for healthcare organizations (eg. BlueHaven, firebrigade, pharmacy), the second one is a booking software for sport clubs and the third one is a competition software for sports hunting. You see very diverse. Include or ignore this info of our products as you like.

The design has to be a bootstrap 4 (or higher) design. We have licenced FontAwesome as iconset. Responsive design should come without saying.

• Starting page, product pages, news section, contact, team, services

```html
<!DOCTYPE html>
<html lang="en">
<head>
<meta charset="utf-8">
<title>velora – Software for every sector</title>
<link href="https://fonts.googleapis.com/css2?family=Rubik:wght@400;500;600;700&display=swap" rel="stylesheet">
<style>
:root{
  --orange:#f47b2a;
  --ink:#262d3a;
  --text:#5d6169;
  --light:#f2f2f2;
  --white:#ffffff;
  --field:#f6f6f6;
  --line:#dcdcdc;
}
*{margin:0;padding:0;box-sizing:border-box}
html,body{width:1200px;height:3499px;overflow:hidden}
body{position:relative;font-family:"Rubik",sans-serif;color:var(--ink);background:var(--white)}
.abs{position:absolute}
a{color:inherit;text-decoration:none}

/* header */
.topline{left:0;top:0;width:1200px;height:5px;background:var(--orange)}
.brand{font-weight:600;letter-spacing:2px;text-transform:uppercase;color:var(--orange);line-height:1}
.header .brand{left:111px;top:28px;font-size:52px}
.nav{left:463px;top:43px;font-size:15px;font-weight:500;text-transform:uppercase}
.nav a{position:absolute;white-space:nowrap}
.nav a.active{color:var(--orange)}
.social{display:flex;gap:6px}
.social span{width:34px;height:34px;border-radius:50%;background:var(--white);box-shadow:0 1px 5px rgba(0,0,0,.18)}
.social span.on{background:var(--orange)}
.header .social{left:976px;top:35px}

/* hero */
.hero{left:0;top:98px;width:1200px;height:660px}
.hero-title{left:628px;top:176px;font-size:41px;font-weight:700;letter-spacing:1px;text-transform:uppercase;white-space:nowrap}
.hero-title em,.h2 em{font-style:normal;color:var(--orange)}
.hero-sub{left:628px;top:238px;width:470px;font-size:19px;font-weight:500;line-height:29px}
.btn{background:var(--orange);color:var(--white);font-weight:500;text-transform:uppercase;display:flex;align-items:center;justify-content:center}
.hero-btn{left:628px;top:322px;width:145px;height:50px;font-size:15px}
.slide-arrow{top:240px;width:24px;height:32px;background:var(--white);display:flex;align-items:center;justify-content:center}

/* headings */
.h2{font-size:36px;font-weight:700;text-transform:uppercase;letter-spacing:.5px;line-height:1}
.p{font-size:14.5px;line-height:26px;color:var(--text)}

/* about */
.about-title{left:111px;top:838px}
.about-p1{left:111px;top:899px;width:453px;text-align:justify}
.about-p2{left:111px;top:1014px;width:453px;text-align:justify}
.about-btn{left:111px;top:1124px;width:132px;height:46px;font-size:15px}
.about-visual{left:637px;top:852px;width:452px;height:326px;background:linear-gradient(135deg,#d3d6da,#7b8088 50%,#4a4d45)}

/* softwares */
.softwares{left:0;top:1282px;width:1200px;height:596px;background:linear-gradient(135deg,#e2661f,#f17d30 55%,#e8712a)}
.softwares .h2{left:0;top:70px;width:1200px;text-align:center;color:var(--white);font-size:38px}
.card{top:161px;width:309px;height:360px;background:var(--white);text-align:center}
.card .icon{position:absolute;left:107px;top:29px;width:94px;height:94px;border-radius:50%;background:var(--ink);display:flex;align-items:center;justify-content:center}
.card h3{position:absolute;left:0;top:150px;width:100%;font-size:19px;font-weight:600;text-transform:uppercase}
.card p{position:absolute;left:12px;top:189px;width:285px;font-size:14.5px;line-height:27px;color:var(--text)}
.more{font-size:13.5px;font-weight:600;color:var(--orange);text-transform:uppercase;display:inline-flex;align-items:center;gap:8px}
.card .more{position:absolute;left:0;width:100%;justify-content:center;top:315px}

/* blog */
.blog{left:0;top:1878px;width:1200px;height:727px;background:var(--light)}
.blog .h2{left:0;top:66px;width:1200px;text-align:center}
.post-img{top:145px;width:473px;height:335px}
.post{top:444px;width:417px;height:213px;background:var(--white);box-shadow:0 4px 14px rgba(0,0,0,.08);text-align:center}
.post .date{position:absolute;left:0;top:23px;width:100%;font-size:15px;color:var(--text);display:flex;justify-content:center;align-items:center;gap:10px}
.post h3{position:absolute;left:0;top:56px;width:100%;font-size:19px;font-weight:600;text-transform:uppercase}
.post p{position:absolute;left:16px;top:91px;width:385px;font-size:13.5px;line-height:25px;color:var(--text)}
.post .more{position:absolute;left:0;width:100%;justify-content:center;top:173px}

/* contact */
.contact-title{left:111px;top:2697px}
.contact-p{left:111px;top:2759px;width:440px;font-size:14.5px;line-height:25px;color:var(--text)}
.info{left:111px;display:flex;align-items:center;gap:24px;font-size:15.5px;font-weight:500}
.info .ring{width:51px;height:51px;border-radius:50%;border:2px solid var(--orange);display:flex;align-items:center;justify-content:center}
.form-card{left:599px;top:2700px;width:490px;height:482px;background:var(--white);box-shadow:0 4px 18px rgba(0,0,0,.1)}
.field{left:22px;width:446px;height:51px;background:var(--field);border:1px solid var(--line);font-size:14.5px;color:var(--ink);padding:16px}
.send{left:22px;top:366px;width:446px;height:50px;font-size:14.5px;font-weight:600}

/* footer */
.footer{left:0;top:3060px;width:1200px;height:439px}
.footer .brand{left:111px;top:215px;font-size:56px}
.footer .social{left:196px;top:300px}
.col-title{font-size:18px;font-weight:600;color:var(--white);text-transform:uppercase;letter-spacing:.3px;white-space:nowrap}
.links{font-size:14.5px;color:var(--white);line-height:29.3px}
.links li{list-style:none;display:flex;align-items:center;gap:16px;white-space:nowrap}
.links li.tall{align-items:flex-start}
.divider{left:111px;top:392px;width:978px;height:1px;background:#4a505c}
.copy{left:0;top:411px;width:1200px;text-align:center;font-size:13.5px;color:var(--white)}
.copy b{color:var(--orange);font-weight:600}
</style>
</head>
<body>

<header class="header">
  <div class="abs topline"></div>
  <div class="abs brand">velora</div>
  <nav class="abs nav">
    <a class="active" style="left:0">Home</a>
    <a style="left:71px">About</a>
    <a style="left:150px">Our softwares</a>
    <a style="left:301px">Blog</a>
    <a style="left:369px">Contact us</a>
  </nav>
  <div class="abs social"><span class="on"></span><span></span><span></span></div>
</header>

<section class="abs hero">
  <svg class="abs" style="left:0;top:0" width="1200" height="660" viewBox="0 0 1200 660">
    <defs>
      <linearGradient id="heroFill" x1="0" y1="0" x2="1" y2="0.4">
        <stop offset="0" stop-color="#8a8f96"/>
        <stop offset=".35" stop-color="#c9cbcd"/>
        <stop offset=".7" stop-color="#e7e7e5"/>
        <stop offset="1" stop-color="#d4d6cf"/>
      </linearGradient>
    </defs>
    <polygon points="0,508 0,0 1200,0 1200,503 299,646" fill="#262d3a"/>
    <g role="img" aria-label="Photo of a smiling young woman with glasses working at a laptop in a bright office">
      <polygon points="0,498 0,0 1200,0 1200,494 299,636" fill="url(#heroFill)"/>
    </g>
    <polygon points="0,507 299,650 1200,507 1200,514 299,658 0,515" fill="#262d3a"/>
  </svg>
  <h1 class="abs hero-title">Welcome to <em>velora</em></h1>
  <p class="abs hero-sub">Lorem ipsum dolor sit amet, consectetur adipis cea elit sed do tempor incididuntea.</p>
  <a class="abs btn hero-btn">Get started</a>
  <div class="abs slide-arrow" style="left:-8px;border-radius:0 16px 16px 0">
    <svg width="10" height="12" viewBox="0 0 10 12"><path d="M7 1 2 6l5 5" stroke="#f47b2a" stroke-width="2.4" fill="none"/></svg>
  </div>
  <div class="abs slide-arrow" style="left:1184px;border-radius:16px 0 0 16px">
    <svg width="10" height="12" viewBox="0 0 10 12"><path d="M3 1l5 5-5 5" stroke="#f47b2a" stroke-width="2.4" fill="none"/></svg>
  </div>
</section>

<section class="about">
  <h2 class="abs h2 about-title">About <em>us</em></h2>
  <p class="abs p about-p1">Sed ut perspiciatis unde omnis iste natus error sit voluptatem acc usantium doloremque laudantium, totam rem aperiam, eaque ipsa quae ab illo inventore veritatis et quasi architecto beatae vitae dicta sunt explicab ipsa luptatem quia volua.</p>
  <p class="abs p about-p2">Lorem ipsum dolor sit amet, consectetur adipiscing elit, sed do eiusmod tempor incididunt ut labore et dolore magna aliqua. Ut enim ad minim veniam quis nostruda.</p>
  <a class="abs btn about-btn">Learn more</a>
  <div class="abs about-visual" role="img" aria-label="Team photos of the developers at their workstations"></div>
</section>

<section class="abs softwares">
  <h2 class="abs h2">Our softwares</h2>

  <article class="abs card" style="left:111px">
    <div class="icon">
      <svg width="46" height="38" viewBox="0 0 46 38" fill="none" stroke="#fff" stroke-width="2"><rect x="3" y="2" width="40" height="26" rx="2"/><path d="M9 22v-5M15 22v-9M21 22v-7M27 22v-11"/><path d="M1 34h44"/><circle cx="36" cy="14" r="4"/></svg>
    </div>
    <h3>Planning software</h3>
    <p>Lorem ipsum dolor sit amet, consectetur adipiscing elit, sed do eiusmod tempor inc ididunt ut labore et dolore magna aliqua. Ut enim ad minimea.</p>
    <a class="more">Learn more <svg width="13" height="13" viewBox="0 0 13 13"><circle cx="6.5" cy="6.5" r="6.5" fill="#f47b2a"/><path d="M5 3.5 8 6.5 5 9.5" stroke="#fff" stroke-width="1.8" fill="none"/></svg></a>
  </article>

  <article class="abs card" style="left:446px">
    <div class="icon">
      <svg width="42" height="42" viewBox="0 0 42 42" fill="none" stroke="#fff" stroke-width="2"><circle cx="21" cy="21" r="8"/><circle cx="21" cy="21" r="15" stroke-dasharray="5 3"/></svg>
    </div>
    <h3>Booking software</h3>
    <p>Lorem ipsum dolor sit amet, consectetur adipiscing elit, sed do eiusmod tempor inc ididunt ut labore et dolore magna aliqua. Ut enim ad minimea.</p>
    <a class="more">Learn more <svg width="13" height="13" viewBox="0 0 13 13"><circle cx="6.5" cy="6.5" r="6.5" fill="#f47b2a"/><path d="M5 3.5 8 6.5 5 9.5" stroke="#fff" stroke-width="1.8" fill="none"/></svg></a>
  </article>

  <article class="abs card" style="left:780px">
    <div class="icon">
      <svg width="42" height="40" viewBox="0 0 42 40" fill="none" stroke="#fff" stroke-width="2"><rect x="3" y="2" width="36" height="30" rx="2"/><path d="M3 9h36M9 15h12M9 20h8"/><circle cx="29" cy="22" r="5"/></svg>
    </div>
    <h3>Competition software</h3>
    <p>Lorem ipsum dolor sit amet, consectetur adipiscing elit, sed do eiusmod tempor inc ididunt ut labore et dolore magna aliqua. Ut enim ad minimea.</p>
    <a class="more">Learn more <svg width="13" height="13" viewBox="0 0 13 13"><circle cx="6.5" cy="6.5" r="6.5" fill="#f47b2a"/><path d="M5 3.5 8 6.5 5 9.5" stroke="#fff" stroke-width="1.8" fill="none"/></svg></a>
  </article>
</section>

<section class="abs blog">
  <h2 class="abs h2">Latest <em>blog</em></h2>

  <div class="abs post-img" style="left:111px;background:linear-gradient(120deg,#3d3a36,#b88a5a 45%,#d9d3c8)" role="img" aria-label="Photo of a woman working on a laptop at a sunny office desk"></div>
  <article class="abs post" style="left:140px">
    <div class="date"><svg width="14" height="14" viewBox="0 0 14 14" fill="#f3b98f"><rect x="0" y="2" width="14" height="12" rx="1"/><rect x="3" y="0" width="2" height="4"/><rect x="9" y="0" width="2" height="4"/><rect x="1.5" y="6" width="11" height="6.5" fill="#fff"/></svg>16 Apr 2022</div>
    <h3>Sed ut perspiciatis unde omnie</h3>
    <p>Lorem ipsum dolor sit amet, consectetur adipiscing elit, sed do eiusmod tempor incididunt ut labore et dolore magna aliqua. Ut enim ad minimea.</p>
    <a class="more">Read more <svg width="13" height="13" viewBox="0 0 13 13"><circle cx="6.5" cy="6.5" r="6.5" fill="#f47b2a"/><path d="M5 3.5 8 6.5 5 9.5" stroke="#fff" stroke-width="1.8" fill="none"/></svg></a>
  </article>

  <div class="abs post-img" style="left:616px;background:linear-gradient(120deg,#e3e6e8,#8d99a3 45%,#4c5560)" role="img" aria-label="Photo of a team meeting around a table in a modern office"></div>
  <article class="abs post" style="left:644px">
    <div class="date"><svg width="14" height="14" viewBox="0 0 14 14" fill="#f3b98f"><rect x="0" y="2" width="14" height="12" rx="1"/><rect x="3" y="0" width="2" height="4"/><rect x="9" y="0" width="2" height="4"/><rect x="1.5" y="6" width="11" height="6.5" fill="#fff"/></svg>16 Apr 2022</div>
    <h3>Sed ut perspiciatis unde omnie</h3>
    <p>Lorem ipsum dolor sit amet, consectetur adipiscing elit, sed do eiusmod tempor incididunt ut labore et dolore magna aliqua. Ut enim ad minimea.</p>
    <a class="more">Read more <svg width="13" height="13" viewBox="0 0 13 13"><circle cx="6.5" cy="6.5" r="6.5" fill="#f47b2a"/><path d="M5 3.5 8 6.5 5 9.5" stroke="#fff" stroke-width="1.8" fill="none"/></svg></a>
  </article>
</section>

<svg class="abs" style="left:0;top:3060px" width="1200" height="439" viewBox="0 0 1200 439">
  <polygon points="0,120 600,14 600,439 0,439" fill="#f47b2a"/>
  <polygon points="0,124 600,24 1200,24 1200,439 0,439" fill="#262d3a"/>
  <polygon points="1089,64 1200,112 1200,122 1089,122" fill="#f47b2a"/>
  <polygon points="1089,70 1200,122 1089,122" fill="#262d3a"/>
</svg>

<section class="contact">
  <h2 class="abs h2 contact-title">Get in <em>touch</em></h2>
  <p class="abs contact-p">Lorem ipsum dolor sit amet, consectetur adipiscing elit, sed do eiusmod tempor incididunt ut laborea.</p>
  <div class="abs info" style="top:2840px">
    <span class="ring"><svg width="12" height="16" viewBox="0 0 12 16"><path d="M6 0a6 6 0 0 0-6 6c0 4.5 6 10 6 10s6-5.5 6-10a6 6 0 0 0-6-6z" fill="#262d3a"/><circle cx="6" cy="6" r="2.2" fill="#fff"/></svg></span>
    Lindenweg 12, 4020 Marbach, Austria
  </div>
  <div class="abs info" style="top:2908px">
    <span class="ring"><svg width="14" height="14" viewBox="0 0 14 14"><path d="M3 0 5.5 3.5 4 5.5c1 2 2.5 3.5 4.5 4.5L10.5 8.5 14 11l-1.5 2.5C6 13.5.5 8 .5 1.5z" fill="#262d3a"/></svg></span>
    +43 7200 55019
  </div>
  <div class="abs info" style="top:2976px">
    <span class="ring"><svg width="15" height="11" viewBox="0 0 15 11"><rect width="15" height="11" rx="1" fill="#262d3a"/><path d="M1 1.5 7.5 6 14 1.5" stroke="#fff" stroke-width="1.3" fill="none"/></svg></span>
    office@velora.at
  </div>

  <form class="abs form-card">
    <div class="abs field" style="top:66px">Full Name</div>
    <div class="abs field" style="top:127px">Phone</div>
    <div class="abs field" style="top:188px">Email</div>
    <div class="abs field" style="top:249px;height:106px">Message</div>
    <div class="abs btn send">Send message</div>
  </form>
</section>

<footer class="abs footer">
  <div class="abs brand">velora</div>
  <div class="abs social"><span class="on"></span><span></span><span></span></div>

  <div class="abs col-title" style="left:487px;top:177px">Navigation</div>
  <ul class="abs links" style="left:487px;top:220px">
    <li><svg width="13" height="13" viewBox="0 0 13 13"><circle cx="6.5" cy="6.5" r="6.5" fill="#f47b2a"/><path d="M5 3.5 8 6.5 5 9.5" stroke="#262d3a" stroke-width="1.8" fill="none"/></svg>Home</li>
    <li><svg width="13" height="13" viewBox="0 0 13 13"><circle cx="6.5" cy="6.5" r="6.5" fill="#f47b2a"/><path d="M5 3.5 8 6.5 5 9.5" stroke="#262d3a" stroke-width="1.8" fill="none"/></svg>About</li>
    <li><svg width="13" height="13" viewBox="0 0 13 13"><circle cx="6.5" cy="6.5" r="6.5" fill="#f47b2a"/><path d="M5 3.5 8 6.5 5 9.5" stroke="#262d3a" stroke-width="1.8" fill="none"/></svg>Our softwares</li>
    <li><svg width="13" height="13" viewBox="0 0 13 13"><circle cx="6.5" cy="6.5" r="6.5" fill="#f47b2a"/><path d="M5 3.5 8 6.5 5 9.5" stroke="#262d3a" stroke-width="1.8" fill="none"/></svg>Blog</li>
    <li><svg width="13" height="13" viewBox="0 0 13 13"><circle cx="6.5" cy="6.5" r="6.5" fill="#f47b2a"/><path d="M5 3.5 8 6.5 5 9.5" stroke="#262d3a" stroke-width="1.8" fill="none"/></svg>Contact Us</li>
  </ul>

  <div class="abs col-title" style="left:692px;top:177px">Other links</div>
  <ul class="abs links" style="left:692px;top:220px">
    <li><svg width="13" height="13" viewBox="0 0 13 13"><circle cx="6.5" cy="6.5" r="6.5" fill="#f47b2a"/><path d="M5 3.5 8 6.5 5 9.5" stroke="#262d3a" stroke-width="1.8" fill="none"/></svg>FAQ</li>
    <li><svg width="13" height="13" viewBox="0 0 13 13"><circle cx="6.5" cy="6.5" r="6.5" fill="#f47b2a"/><path d="M5 3.5 8 6.5 5 9.5" stroke="#262d3a" stroke-width="1.8" fill="none"/></svg>Privacy Policy</li>
    <li><svg width="13" height="13" viewBox="0 0 13 13"><circle cx="6.5" cy="6.5" r="6.5" fill="#f47b2a"/><path d="M5 3.5 8 6.5 5 9.5" stroke="#262d3a" stroke-width="1.8" fill="none"/></svg>Terms Of use</li>
    <li><svg width="13" height="13" viewBox="0 0 13 13"><circle cx="6.5" cy="6.5" r="6.5" fill="#f47b2a"/><path d="M5 3.5 8 6.5 5 9.5" stroke="#262d3a" stroke-width="1.8" fill="none"/></svg>Legal Support</li>
  </ul>

  <div class="abs col-title" style="left:925px;top:177px">Contact info</div>
  <ul class="abs links" style="left:930px;top:220px;width:230px">
    <li class="tall"><svg width="10" height="14" style="margin-top:7px;flex:none" viewBox="0 0 12 16"><path d="M6 0a6 6 0 0 0-6 6c0 4.5 6 10 6 10s6-5.5 6-10a6 6 0 0 0-6-6z" fill="#f47b2a"/><circle cx="6" cy="6" r="2.2" fill="#262d3a"/></svg><span style="line-height:25px;padding-top:2px">Lindenweg 12,<br>4020 Marbach, Austria</span></li>
    <li><svg width="12" height="12" viewBox="0 0 14 14"><path d="M3 0 5.5 3.5 4 5.5c1 2 2.5 3.5 4.5 4.5L10.5 8.5 14 11l-1.5 2.5C6 13.5.5 8 .5 1.5z" fill="#f47b2a"/></svg>+43 7200 55019</li>
    <li><svg width="13" height="10" viewBox="0 0 15 11"><rect width="15" height="11" rx="1" fill="#f47b2a"/><path d="M1 1.5 7.5 6 14 1.5" stroke="#262d3a" stroke-width="1.3" fill="none"/></svg>office@velora.at</li>
  </ul>

  <div class="abs divider"></div>
  <p class="abs copy">© 2022 <b>VELORA</b> &nbsp;|&nbsp; All Rights reserved</p>
</footer>

</body>
</html>
```